Heron Loan Partners Business Card

We need a business card design for our mortgage servicing company. In addition to servicing the loans of homeowners, we help homeowners with purchasing their homes and any mortgage refinancing. We would like to see designs that use the colors in the logo attached below (gold-ish yellow and navy blue), and any other design you deem fit! The design should communicate a simpler life with smart mortgages provided by Heron.

```html
<!DOCTYPE html>
<html lang="en">
<head>
<meta charset="utf-8">
<title>Heron Loan Partners – Business Card</title>
<link rel="stylesheet" href="https://fonts.googleapis.com/css2?family=Poppins:wght@400&family=Tinos:wght@700&display=swap">
<style>
  :root {
    --backdrop: #777777;
    --navy: #261f51;
    --gold: #e0b43f;
    --paper: #ffffff;
    --ink: #111111;
    --rule: #b9b9b9;
    --shadow: rgba(0, 0, 0, 0.85);
  }
  * { margin: 0; padding: 0; box-sizing: border-box; }
  html, body {
    width: 1065px;
    height: 1200px;
    overflow: hidden;
    background: var(--backdrop);
  }
  .canvas {
    position: relative;
    width: 1065px;
    height: 1200px;
  }
  .card {
    position: absolute;
    width: 583px;
    height: 362px;
    box-shadow: 3px 3px 2px var(--shadow);
  }
  .card--front {
    left: 292px;
    top: 218px;
    background: var(--paper);
    border-radius: 0 181px 181px 0;
  }
  .card--back {
    left: 263px;
    top: 623px;
    background: var(--navy);
    border-radius: 181px 0 0 181px;
  }
  .company-name {
    position: absolute;
    font-family: "Poppins", Arial, sans-serif;
    font-weight: 400;
    line-height: 1.25;
  }
  .card--front .company-name {
    left: 40px;
    top: 95px;
    width: 140px;
    font-size: 20px;
    color: var(--navy);
  }
  .card--back .company-name {
    right: 48px;
    bottom: 44px;
    font-size: 22px;
    color: var(--paper);
    white-space: nowrap;
  }
  .divider {
    position: absolute;
    left: 198px;
    top: 95px;
    width: 1px;
    height: 173px;
    background: var(--rule);
  }
  .details {
    position: absolute;
    left: 226px;
    top: 93px;
    font-family: "Poppins", Arial, sans-serif;
    color: var(--ink);
  }
  .person-name {
    font-family: "Tinos", "Times New Roman", serif;
    font-weight: 700;
    font-size: 22px;
    line-height: 23px;
    color: var(--navy);
    letter-spacing: 0.2px;
  }
  .person-name .surname { color: var(--gold); }
  .person-role {
    font-size: 17px;
    line-height: 20px;
    color: var(--navy);
  }
  .contact-list {
    list-style: none;
    margin-top: 14px;
  }
  .contact-item {
    display: flex;
    align-items: center;
    gap: 6px;
    font-size: 17px;
    line-height: 21px;
  }
  .contact-icon {
    width: 15px;
    height: 15px;
    flex: none;
  }
  .accent { color: var(--gold); }
  .address {
    font-style: normal;
    font-size: 17px;
    line-height: 21px;
    margin-top: 13px;
  }
</style>
</head>
<body>
<main class="canvas">

  <section class="card card--front" aria-label="Business card front">
    <p class="company-name">Heron Loan Partners</p>
    <span class="divider"></span>
    <div class="details">
      <h1 class="person-name">DANIEL <span class="surname">CARTER</span></h1>
      <p class="person-role">Managing Director</p>
      <ul class="contact-list">
        <li class="contact-item">
          <svg class="contact-icon" viewBox="0 0 24 24" aria-hidden="true">
            <path fill="none" stroke="var(--gold)" stroke-width="2.2" stroke-linejoin="round" d="M6 3 L9.5 3 L11 8 L8.5 9.5 C9.7 12.3 11.7 14.3 14.5 15.5 L16 13 L21 14.5 L21 18 C21 19.7 19.7 21 18 21 C10 21 3 14 3 6 C3 4.3 4.3 3 6 3 Z"/>
            <path fill="none" stroke="var(--gold)" stroke-width="2" stroke-linecap="round" d="M14 3.5 A7 7 0 0 1 20.5 10 M14 7 A3.5 3.5 0 0 1 17 10"/>
          </svg>
          <span>044-555 018 274</span>
        </li>
        <li class="contact-item">
          <svg class="contact-icon" viewBox="0 0 24 24" aria-hidden="true">
            <rect x="1" y="5" width="22" height="14" fill="var(--gold)"/>
            <path fill="none" stroke="var(--paper)" stroke-width="1.6" d="M1 5 L12 13 L23 5"/>
          </svg>
          <span>info@heronloan.com</span>
        </li>
        <li class="contact-item">
          <svg class="contact-icon" viewBox="0 0 24 24" aria-hidden="true">
            <g fill="none" stroke="var(--gold)" stroke-width="1.8">
              <circle cx="12" cy="12" r="10"/>
              <ellipse cx="12" cy="12" rx="4.5" ry="10"/>
              <path d="M2 12 H22 M4 7 H20 M4 17 H20"/>
            </g>
          </svg>
          <span>www.<span class="accent">heronloanpartners.</span>com</span>
        </li>
      </ul>
      <address class="address">421, Address line goes here<br>45452,Country Name</address>
    </div>
  </section>

  <section class="card card--back" aria-label="Business card back">
    <p class="company-name">Heron Loan Partners</p>
  </section>

</main>
</body>
</html>
```